Executive recruiting firm in need of business card design

Executive recruiting firm looking for a sleek, classy and modern business card design; card itself will be square shape, rounded edges and soft touch paper, our colors are dark blues in the navy color scale, silvers and grays. Reference our website for a better idea of our company's feel and goals at Tarvex-Up.com - our company message is "Employee Engagement Begins at Recruitment" this should be on the card

```html
<!DOCTYPE html>
<html lang="en">
<head>
<meta charset="utf-8">
<title>Tarvex Up – Business Card</title>
<link href="https://fonts.googleapis.com/css2?family=Roboto:wght@400;500;700&display=swap" rel="stylesheet">
<style>
  :root {
    --navy: #15174a;
    --navy-deep: #12143f;
    --white: #ffffff;
    --paper: #fafafa;
    --stage: #e6e6e6;
    --grey-text: #6b6b6b;
    --grey-band: #7a7a7a;
    --silver: #c4c6d6;
  }
  html, body {
    margin: 0;
    padding: 0;
    width: 1200px;
    height: 624px;
    overflow: hidden;
    background: var(--stage);
  }
  .canvas {
    position: relative;
    width: 1200px;
    height: 624px;
    font-family: "Roboto", sans-serif;
  }
  .card {
    position: absolute;
    top: 152px;
    width: 320px;
    height: 320px;
    border-radius: 16px;
    overflow: hidden;
  }
  .card--front { left: 218px; background: var(--navy); }
  .card--back { left: 662px; background: var(--paper); }

  .front-scene {
    position: absolute;
    inset: 0;
    background: radial-gradient(ellipse at 45% 55%, #1b1e55 0%, var(--navy) 55%, var(--navy-deep) 100%);
  }

  .brand {
    position: absolute;
    white-space: nowrap;
  }
  .brand__name {
    display: block;
    font-weight: 500;
    font-size: 30px;
    letter-spacing: 3px;
    line-height: 1;
  }
  .brand__tagline {
    display: block;
    font-weight: 400;
    font-size: 8px;
    letter-spacing: 2px;
    margin-top: 6px;
  }
  .brand--front {
    left: 0;
    right: 0;
    top: 128px;
    text-align: center;
    color: var(--white);
  }
  .brand--back {
    right: 30px;
    top: 62px;
    text-align: right;
    color: var(--navy);
  }

  .message {
    position: absolute;
    left: 0;
    right: 0;
    top: 196px;
    margin: 0;
    text-align: center;
    font-size: 10px;
    letter-spacing: 1px;
    color: var(--silver);
    white-space: nowrap;
  }

  .person {
    position: absolute;
    left: 19px;
    top: 142px;
  }
  .person__name {
    margin: 0;
    font-size: 18px;
    font-weight: 700;
    color: var(--navy);
  }
  .person__role {
    margin: 4px 0 0;
    font-size: 12px;
    color: var(--grey-text);
  }

  .contact {
    position: absolute;
    left: 19px;
    top: 209px;
    font-size: 12.5px;
    color: var(--grey-text);
    list-style: none;
    margin: 0;
    padding: 0;
  }
  .contact__row {
    display: flex;
    align-items: center;
    height: 18px;
  }
  .contact__icon { width: 12px; height: 10px; margin-right: 14px; }
  .contact__address { margin-top: 8px; line-height: 17px; }

  .footer-band {
    position: absolute;
    left: 0;
    bottom: 0;
    width: 320px;
    height: 34px;
  }
  .footer-band__url {
    position: absolute;
    right: 20px;
    bottom: 9px;
    font-weight: 500;
    font-size: 12px;
    color: var(--white);
  }
</style>
</head>
<body>
<div class="canvas">

  <section class="card card--front">
    <div class="front-scene" role="img" aria-label="Dimmed photo of an executive standing by an office window, tinted navy"></div>
    <div class="brand brand--front">
      <span class="brand__name">TARVEX UP</span>
      <span class="brand__tagline">talent acquisition</span>
    </div>
    <p class="message">Employee Engagement Begins at Recruitment</p>
  </section>

  <section class="card card--back">
    <div class="brand brand--back">
      <span class="brand__name">TARVEX UP</span>
      <span class="brand__tagline">talent acquisition</span>
    </div>

    <div class="person">
      <h1 class="person__name">Employee Name</h1>
      <p class="person__role">Managing Director</p>
    </div>

    <ul class="contact">
      <li class="contact__row">
        <svg class="contact__icon" viewBox="0 0 12 10" aria-hidden="true">
          <path d="M0 3 Q6 -1 12 3 L10.5 4.5 L8.5 3.5 L8.5 2.5 Q6 1.8 3.5 2.5 L3.5 3.5 L1.5 4.5 Z" fill="var(--navy)"/>
          <path d="M3 4.5 L9 4.5 L11 9.5 L1 9.5 Z" fill="var(--navy)"/>
        </svg>
        00-1234-1234-55
      </li>
      <li class="contact__row">
        <svg class="contact__icon" viewBox="0 0 12 10" aria-hidden="true">
          <rect x="0.5" y="1" width="11" height="8" fill="none" stroke="var(--navy)" stroke-width="1.2"/>
          <path d="M0.5 1 L6 5.5 L11.5 1 M0.5 9 L4.5 4.5 M11.5 9 L7.5 4.5" fill="none" stroke="var(--navy)" stroke-width="1.2"/>
        </svg>
        employee@tarvex-up.com
      </li>
      <li class="contact__address">248 W Meridian Ave, Larkfield,<br>CA 91270, USA</li>
    </ul>

    <svg class="footer-band" viewBox="0 0 320 34" aria-hidden="true">
      <rect x="0" y="18" width="320" height="16" fill="var(--grey-band)"/>
      <polygon points="138,0 320,0 320,34 126,34" fill="var(--navy)"/>
    </svg>
    <span class="footer-band__url">www.tarvex-up.com</span>
  </section>

</div>
</body>
</html>
```